Coffee Bag Design for Tollbury Coffee

We’re excited to invite you to help us bring Tollbury Coffee to life on grocery store shelves with a design that embodies our mission of spreading goodness and creating a lasting impact. Tollbury Coffee represents warmth, positivity, and the power of small actions to create ripples of goodness. Each cup not only offers a rich, gourmet coffee experience but also gives back to the community, with $2 from each bag supporting local food banks.

To reflect this vision, we’d love for the design to feature a dark (greyish) blue as the base color to convey depth and quality, complemented by a vibrant light blue that will catch the eye and add energy. Tan or gold accents could add an elegant touch and a feeling of warmth. We are aiming for a look that feels uplifting and engaging, with simplicity and elegance, yet stands out amid other brands on the shelf.

I am attaching the dimension of the bag.

Other information that needs to be listed:
Ingredients: 100% Arabica Coffee
Net Wt. 12 oz. (340 g)
Roasted and distributed by:
Name
Address
email

Text on the back of the bag:
Tollbury Coffee is crafted with a belief that kindness and positivity can spread, touching countless lives with every sip. This gourmet blend delivers a rich taste experience while giving back, as $2 from each bag sold is donated to local food banks to help those in need. Enjoy the warmth and goodness in each cup, knowing you’re making a difference with every purchase.

Thank you!

```html
<!DOCTYPE html>
<html lang="en">
<head>
<meta charset="utf-8">
<title>Tollbury Coffee – Bag Dieline</title>
<link rel="stylesheet" href="https://fonts.googleapis.com/css2?family=Montserrat:ital,wght@0,400;0,600;0,700;1,400;1,700&family=Open+Sans:wght@400&display=swap">
<style>
  :root{
    --page:#ffffff;
    --navy:#2a3847;
    --steel:#43809f;
    --olive:#939369;
    --sky:#5bc4ef;
    --card:#b4d8e6;
    --gold:#c9a86a;
    --ink:#222222;
    --guide:#333333;
  }
  html,body{margin:0;padding:0;overflow:hidden;background:var(--page);}
  .canvas{width:1199px;height:1200px;position:relative;}
  svg{display:block;}
  .dim-label{font-family:"Open Sans",sans-serif;font-size:28px;fill:var(--ink);}
  .legend{font-family:"Open Sans",sans-serif;font-size:15px;fill:var(--ink);}
  .guide{stroke:var(--guide);stroke-width:1;fill:none;}
  .brand-name{font-family:"Montserrat",sans-serif;font-weight:700;fill:var(--sky);}
  .blend-title{font-family:"Montserrat",sans-serif;font-weight:700;font-size:19px;fill:var(--navy);letter-spacing:.5px;}
  .card-head{font-family:"Montserrat",sans-serif;font-weight:600;font-size:11.5px;fill:var(--navy);}
  .card-small{font-family:"Montserrat",sans-serif;font-weight:700;font-style:italic;font-size:7.5px;fill:var(--navy);}
  .card-tiny{font-family:"Montserrat",sans-serif;font-weight:700;font-size:7.5px;fill:var(--navy);letter-spacing:.3px;}
  .card-label{font-family:"Montserrat",sans-serif;font-weight:400;font-style:italic;font-size:7.5px;fill:var(--navy);}
  .card-foot{font-family:"Montserrat",sans-serif;font-weight:600;font-size:13px;fill:var(--navy);}
  .band-sky{fill:var(--sky);}
  .base-navy{fill:var(--navy);}
</style>
</head>
<body>
<div class="canvas">
<svg width="1199" height="1200" viewBox="0 0 1199 1200" xmlns="http://www.w3.org/2000/svg">
  <defs>
    <linearGradient id="side-sky" x1="0" y1="0" x2="1" y2="1">
      <stop offset="0" stop-color="#2a3847"/>
      <stop offset=".35" stop-color="#43809f"/>
      <stop offset=".7" stop-color="#939369"/>
      <stop offset="1" stop-color="#2a3847"/>
    </linearGradient>
    <linearGradient id="front-sky" x1="0" y1="0" x2="0" y2="1">
      <stop offset="0" stop-color="#43809f"/>
      <stop offset=".55" stop-color="#939369"/>
      <stop offset="1" stop-color="#2a3847"/>
    </linearGradient>
    <radialGradient id="cup-glow" cx="0.5" cy="0.5" r="0.5">
      <stop offset="0" stop-color="#eaf4f8" stop-opacity=".6"/>
      <stop offset="1" stop-color="#2a3847" stop-opacity="0"/>
    </radialGradient>
    <linearGradient id="cup-fill" x1="0" y1="0" x2="0" y2="1">
      <stop offset="0" stop-color="#5bc4ef"/>
      <stop offset="1" stop-color="#d4b58c"/>
    </linearGradient>
    <filter id="card-shadow" x="-10%" y="-10%" width="120%" height="130%">
      <feDropShadow dx="0" dy="3" stdDeviation="3" flood-color="#000" flood-opacity=".35"/>
    </filter>
  </defs>

  <g class="legend-block">
    <text class="legend" x="133" y="192">Bleed : 0.125 in</text>
    <line class="guide" x1="133" y1="211" x2="173" y2="211"/>
    <text class="legend" x="183" y="217">Cut Line</text>
  </g>

  <g class="side-panel">
    <rect class="base-navy" x="301" y="296" width="225" height="684"/>
    <rect class="side-pattern" role="img" aria-label="Decorative radiating stripes in steel blue and olive" x="301" y="296" width="225" height="354" fill="url(#side-sky)"/>
    <rect class="band-sky" x="301" y="834" width="225" height="64"/>
    <rect class="band-sky" x="301" y="907" width="225" height="73"/>
  </g>

  <g class="front-panel">
    <rect class="base-navy" x="644" y="296" width="378" height="684"/>
    <rect class="front-pattern" role="img" aria-label="Decorative radiating stripes in steel blue and olive behind the cup" x="644" y="296" width="378" height="338" fill="url(#front-sky)"/>
    <circle cx="855" cy="590" r="110" fill="url(#cup-glow)"/>
    <rect class="hero-art" role="img" aria-label="Illustration: steaming blue coffee cup resting on an open hand" x="775" y="488" width="165" height="162" rx="24" fill="url(#cup-fill)" opacity=".9"/>

    <rect class="band-sky" x="644" y="834" width="378" height="64"/>
    <rect class="band-sky" x="644" y="907" width="378" height="73"/>

    <rect class="inner-frame" x="672" y="323" width="323" height="623" rx="14" fill="none" stroke="var(--gold)" stroke-width="1" opacity=".8"/>

    <text class="brand-name" x="841" y="705" text-anchor="middle" font-size="40">TOLLBURY</text>
    <text class="brand-name" x="841" y="743" text-anchor="middle" font-size="30">COFFEE</text>

    <circle class="quality-badge" cx="720" cy="756" r="33" fill="var(--gold)"/>

    <g class="product-card">
      <rect x="681" y="803" width="306" height="132" fill="var(--card)" filter="url(#card-shadow)"/>
      <text class="blend-title" x="829" y="831" text-anchor="middle">MORNING BLEND</text>
      <line x1="688" y1="840" x2="974" y2="840" stroke="var(--navy)" stroke-width="1"/>
      <line x1="853" y1="840" x2="853" y2="902" stroke="var(--navy)" stroke-width="1"/>
      <line x1="688" y1="902" x2="974" y2="902" stroke="var(--navy)" stroke-width="1"/>

      <text class="card-head" x="692" y="856">NOTES</text>
      <text class="card-small" x="692" y="868">HAZELNUT, CARAMEL &amp;</text>
      <text class="card-small" x="692" y="879">BLUEBERRY</text>

      <text class="card-head" x="861" y="856">ROAST</text>
      <g class="roast-beans">
        <g transform="translate(876,874) rotate(35)">
          <ellipse rx="6" ry="9" fill="var(--navy)"/>
          <path d="M0,-8 C-3,-3 3,3 0,8" stroke="var(--card)" stroke-width="1.2" fill="none"/>
        </g>
        <g transform="translate(916,874) rotate(35)">
          <ellipse rx="6" ry="9" fill="none" stroke="var(--navy)" stroke-width="1.2"/>
          <path d="M0,-8 C-3,-3 3,3 0,8" stroke="var(--navy)" stroke-width="1.2" fill="none"/>
        </g>
        <g transform="translate(956,874) rotate(35)">
          <ellipse rx="6" ry="9" fill="none" stroke="var(--navy)" stroke-width="1.2"/>
          <path d="M0,-8 C-3,-3 3,3 0,8" stroke="var(--navy)" stroke-width="1.2" fill="none"/>
        </g>
      </g>
      <text class="card-small" x="875" y="893" text-anchor="middle">LIGHT</text>
      <text class="card-label" x="915" y="893" text-anchor="middle">MEDIUM</text>
      <text class="card-label" x="955" y="893" text-anchor="middle">DARK</text>

      <text class="card-foot" x="694" y="922">WHOLE BEAN COFFEE</text>
      <text class="card-tiny" x="941" y="916" text-anchor="middle">NET WT</text>
      <text class="card-tiny" x="941" y="926" text-anchor="middle">12 OZ.(340 G)</text>
    </g>
  </g>

  <g class="crop-marks">
    <line class="guide" x1="310" y1="268" x2="310" y2="296"/>
    <line class="guide" x1="517" y1="268" x2="517" y2="296"/>
    <line class="guide" x1="310" y1="980" x2="310" y2="1008"/>
    <line class="guide" x1="517" y1="980" x2="517" y2="1008"/>
    <line class="guide" x1="272" y1="305" x2="301" y2="305"/>
    <line class="guide" x1="526" y1="305" x2="554" y2="305"/>
    <line class="guide" x1="272" y1="971" x2="301" y2="971"/>
    <line class="guide" x1="526" y1="971" x2="554" y2="971"/>

    <line class="guide" x1="653" y1="268" x2="653" y2="296"/>
    <line class="guide" x1="1013" y1="268" x2="1013" y2="296"/>
    <line class="guide" x1="653" y1="980" x2="653" y2="1008"/>
    <line class="guide" x1="1013" y1="980" x2="1013" y2="1008"/>
    <line class="guide" x1="616" y1="305" x2="644" y2="305"/>
    <line class="guide" x1="1022" y1="305" x2="1050" y2="305"/>
    <line class="guide" x1="616" y1="971" x2="644" y2="971"/>
    <line class="guide" x1="1022" y1="971" x2="1050" y2="971"/>
  </g>

  <g class="dimensions">
    <text class="dim-label" x="407" y="275" text-anchor="middle">2.875in</text>
    <text class="dim-label" x="836" y="275" text-anchor="middle">5in</text>
    <text class="dim-label" transform="translate(271,652) rotate(-90)" text-anchor="middle">9.25in</text>
    <text class="dim-label" transform="translate(626,652) rotate(-90)" text-anchor="middle">9.25in</text>
  </g>
</svg>
</div>
</body>
</html>
```